Logo and Card design for KRV Home Solutions LLC

I need an edgier logo and business card designs. Current logo attached. I like the colors below. I would like the logo to incorporate a home in the design.
Title = Principal-Acquisitions
Email:KRVHOMESOLUTIONS@fernmail.example
555-214-0937
facebook
IG
2 sided business card with the front being contact info a slogan about selling a home fast. The back incorporating What we do. Buy houses, land, or commercial property as is. We find solutions to make the process of selling simple and fair.

Target Market(s)

Motivated house sellers.

Industry/Entity Type

Business

Contact Information for Business Card

Who we are: We are a Faith based Real Estate Investment Company. We pay cash for homes in any condition and can close quick. Whatever the reason you need to sell fast, we can help. We believe in creating win-win solutions to help you in your time of need. We care! We can help!

Logo Text

KRV Home Solutions LLC

Font styles to use
Sans Serif

Colors
33a6d7
0355a3
85abd2
cee9f5
9d9d9d
b2b2b2
ffffff

Requirements
Must have
• Old logo attached. I want something edgier.
• Company name, phone number, description on the back of what we can do. Pay all cash. Buy in as is condition. No fees,Commisions or closing costs.Close quick. No hassles with solutions to meet your unique situation.
• Call today for an offer within 24 hours.

```html
<!DOCTYPE html>
<html lang="en">
<head>
<meta charset="utf-8">
<title>KRV Home Solutions – Business Card</title>
<link href="https://fonts.googleapis.com/css2?family=Roboto:wght@400;500;700&family=Roboto+Condensed:wght@400;700&display=swap" rel="stylesheet">
<style>
  :root {
    --navy: #1e3566;
    --navy-ink: #1f3a7a;
    --ink: #3c3c3c;
    --grey: #5a5a5a;
    --white: #ffffff;
    --backdrop: #2e2e2e;
  }
  * { box-sizing: border-box; margin: 0; padding: 0; }
  html, body { width: 1200px; height: 960px; overflow: hidden; }
  body { background: var(--backdrop); position: relative; font-family: "Roboto", Arial, sans-serif; }

  .card { position: absolute; width: 600px; height: 342px; overflow: hidden; }
  .card--front { left: 314px; top: 113px; background: #eef2f4; }
  .card--back { left: 311px; top: 472px; background: var(--navy); color: var(--white); text-align: center; }

  .front-photo {
    position: absolute; inset: 0;
    background:
      linear-gradient(180deg, rgba(214,228,236,.55) 0%, rgba(238,242,244,.4) 55%, rgba(206,222,206,.6) 100%),
      linear-gradient(90deg, #e9eef1 0%, #dfe6e8 45%, #d5e1d8 100%);
  }
  .accent-bar { position: absolute; left: 0; top: 45px; width: 14px; height: 41px; background: var(--navy-ink); }

  .person-name { position: absolute; left: 44px; top: 44px; font-family: "Roboto Condensed", Arial, sans-serif; font-weight: 700; font-size: 23px; color: var(--navy-ink); letter-spacing: .3px; }
  .person-title { position: absolute; left: 44px; top: 70px; font-size: 15px; font-weight: 500; color: var(--grey); }

  .contact-list { position: absolute; left: 44px; top: 146px; list-style: none; }
  .contact-list li { display: flex; align-items: center; gap: 8px; font-size: 14.5px; color: var(--ink); height: 19px; }
  .contact-list svg { width: 13px; height: 13px; fill: var(--navy-ink); flex: none; }

  .offer-list { position: absolute; left: 44px; top: 215px; list-style: none; font-family: "Roboto Condensed", Arial, sans-serif; font-size: 14.5px; color: var(--ink); line-height: 18px; }
  .offer-list li { position: relative; padding-left: 12px; }
  .offer-list li::before { content: ""; position: absolute; left: 0; top: 7px; width: 5px; height: 5px; border-radius: 50%; background: var(--navy-ink); }

  .brand-front { position: absolute; left: 374px; top: 230px; width: 190px; display: flex; align-items: center; gap: 8px; font-weight: 700; font-size: 22px; color: var(--navy-ink); line-height: 1.1; }
  .brand-back { display: inline-flex; align-items: center; gap: 8px; margin-top: 80px; font-weight: 700; font-size: 28px; color: var(--white); }
  .brand-mark { width: 14px; height: 14px; background: currentColor; flex: none; }

  .section-head { font-weight: 700; font-size: 15px; margin-top: 18px; }
  .card--back p { font-size: 14.5px; line-height: 18px; margin-top: 4px; }
  .brand-back + .section-head { margin-top: 24px; }
</style>
</head>
<body>
  <section class="card card--front">
    <div class="front-photo" role="img" aria-label="Faded photo of a modern two-storey house with trees and a lawn"></div>
    <div class="accent-bar"></div>
    <h1 class="person-name">MARCUS REED</h1>
    <div class="person-title">Principal-Acquisitions</div>

    <ul class="contact-list">
      <li><svg viewBox="0 0 24 24"><path d="M6.6 10.8a15.1 15.1 0 0 0 6.6 6.6l2.2-2.2a1 1 0 0 1 1-.25 11.4 11.4 0 0 0 3.6.57 1 1 0 0 1 1 1V20a1 1 0 0 1-1 1A17 17 0 0 1 3 4a1 1 0 0 1 1-1h3.5a1 1 0 0 1 1 1c0 1.25.2 2.45.57 3.57a1 1 0 0 1-.25 1z"/></svg>555-214-0937</li>
      <li><svg viewBox="0 0 24 24"><path d="M2 5h20v14H2z M4 7v.5l8 5 8-5V7l-8 5z" fill-rule="evenodd"/></svg>KRVHOMESOLUTIONS@fernmail.example</li>
      <li><svg viewBox="0 0 24 24"><circle cx="12" cy="12" r="10"/></svg>KRVHOMESOLUTIONS.example</li>
    </ul>

    <ul class="offer-list">
      <li>Pay all cash. Buy in as is condition</li>
      <li>No fees,Commisions or closing costs</li>
      <li>Close quick. No hassles with<br>solutions to meet your unique situation</li>
      <li>Call today for an offer within 24 hours</li>
    </ul>

    <div class="brand-front"><span class="brand-mark"></span><span>KRV Home Solutions</span></div>
  </section>

  <section class="card card--back">
    <div class="brand-back"><span class="brand-mark"></span><span>KRV Home Solutions</span></div>
    <h2 class="section-head">WHO WE ARE</h2>
    <p>We are a Faith based Real Estate Investment Company. We pay cash for<br>homes in any condition and can close quick. Whatever the reason you need<br>to sell fast, we can help. We believe in creating win-win solutions to help</p>
    <h2 class="section-head">WHAT WE DO</h2>
    <p>Buy houses, land, or commercial property as is.<br>We find solutions to make the process of selling simple and fair.</p>
  </section>
</body>
</html>
```